Business card design for holistic health care clinic

We need a double-sided business card design for our holistic health care clinic that integrates our logo design and also its color scheme. My business is called Valmira. It is an integrative medicine clinic. You have already done the logo for me. Please ensure an elegant and upscale design that is not cluttered, but still has all the necessary information (please see below for details).

Target Market(s)

Wellness, fitness, rehabilitation for educated, well-traveled open-minded clients who are focused on natural, organic, balanced and preventive healthcare and lifestyle.

Industry/Entity Type

Medical

Contact Information for Business Card

Modern, clean.

Number of Pages Required

1 page

Font styles to use
Serif
Sans Serif

Colors

Designer to choose colors to be used in the design.

Requirements
Must have
• Logo on one side, all other information on the other side.
• Other information should include:
• Tobias Wrenfeld - DOE, CPT, LMT
• 4100 East Marrow Drive
• Austin, TX 78119
• 512 555 0148
• 818 555 0192
• info@ValmiraHealth.example
• t.wrenfeld@ValmiraHealth.example
Nice to have
• Darker background on front - but not totally black - shaded/dark gray.

```html
<!DOCTYPE html>
<html lang="en">
<head>
<meta charset="utf-8">
<title>Valmira – Business Card</title>
<link rel="stylesheet" href="https://fonts.googleapis.com/css2?family=Nunito+Sans:wght@400;600;700;800&display=swap">
<style>
  :root {
    --backdrop: #8c8c8c;
    --card-dark: #111114;
    --brand-blue: #1a90d2;
    --wave-light: #1096d6;
    --wave-dark: #0a7db9;
    --text-light: #f2f2f2;
    --white: #ffffff;
  }
  * { margin: 0; padding: 0; box-sizing: border-box; }
  html, body {
    width: 1200px; height: 900px; overflow: hidden;
    background: var(--backdrop);
    font-family: "Nunito Sans", Arial, sans-serif;
  }
  .stage { position: relative; width: 1200px; height: 900px; }

  .card { position: absolute; top: 200px; width: 310px; height: 502px; overflow: hidden; }

  .card--front {
    left: 265px;
    background: var(--card-dark);
    border-radius: 52px 0 52px 0;
  }
  .card--back {
    left: 641px;
    border-radius: 0 52px 0 52px;
  }

  .brand { position: absolute; left: 0; width: 100%; text-align: center; }
  .brand__name {
    font-weight: 800; font-size: 46px; letter-spacing: 1px; line-height: 1;
  }
  .brand__tagline {
    font-weight: 700; font-size: 15.5px; margin-top: 6px; letter-spacing: 0.2px;
  }
  .card--front .brand { top: 100px; color: var(--brand-blue); }
  .card--back .brand { top: 385px; color: var(--white); }

  .holder {
    position: absolute; left: 26px; top: 284px;
    color: var(--brand-blue); font-weight: 700; font-size: 17px;
  }
  .holder__credentials { font-size: 12px; font-weight: 700; }

  .address {
    position: absolute; left: 23px; top: 326px;
    color: var(--text-light); font-size: 13.5px; line-height: 21px;
  }

  .contacts {
    position: absolute; left: 23px; top: 383px; list-style: none;
    color: var(--text-light); font-size: 13.5px; line-height: 21px;
  }
  .contacts__item { display: flex; align-items: center; gap: 7px; }
  .contacts__icon { width: 11px; height: 11px; fill: var(--brand-blue); flex: none; }

  .wave-field {
    position: absolute; inset: 0;
    background:
      radial-gradient(ellipse 70% 30% at 30% 35%, var(--wave-dark), transparent 70%),
      radial-gradient(ellipse 60% 40% at 80% 70%, var(--wave-dark), transparent 70%),
      linear-gradient(160deg, var(--wave-light) 0%, var(--wave-dark) 55%, var(--wave-light) 100%);
  }
</style>
</head>
<body>
<main class="stage">

  <section class="card card--front">
    <div class="brand">
      <div class="brand__name">VALMIRA</div>
      <div class="brand__tagline">Integrative Holistic Medicine</div>
    </div>

    <p class="holder">Tobias Wrenfeld <span class="holder__credentials">- DOE, CPT, LMT</span></p>

    <address class="address" style="font-style:normal">
      4100 East Marrow Drive<br>
      Austin, TX 78119
    </address>

    <ul class="contacts">
      <li class="contacts__item">
        <svg class="contacts__icon" viewBox="0 0 24 24"><path d="M6.6 10.8a15.1 15.1 0 0 0 6.6 6.6l2.2-2.2c.3-.3.7-.4 1-.2 1.1.4 2.3.6 3.6.6.6 0 1 .4 1 1V20c0 .6-.4 1-1 1A17 17 0 0 1 3 4c0-.6.4-1 1-1h3.5c.6 0 1 .4 1 1 0 1.3.2 2.5.6 3.6.1.3 0 .7-.2 1z"/></svg>
        512 555 0148
      </li>
      <li class="contacts__item">
        <svg class="contacts__icon" viewBox="0 0 24 24"><path d="M7 1h10a2 2 0 0 1 2 2v18a2 2 0 0 1-2 2H7a2 2 0 0 1-2-2V3a2 2 0 0 1 2-2zm0 3v14h10V4zm5 15.5a1.2 1.2 0 1 0 0 2.4 1.2 1.2 0 0 0 0-2.4z"/></svg>
        818 555 0192
      </li>
      <li class="contacts__item">
        <svg class="contacts__icon" viewBox="0 0 24 24"><path d="M2 5h20v2l-10 6L2 7zm0 4 10 6 10-6v10H2z"/></svg>
        info@ValmiraHealth.example
      </li>
      <li class="contacts__item">
        <svg class="contacts__icon" viewBox="0 0 24 24"><path d="M12 1a11 11 0 1 0 0 22 11 11 0 0 0 0-22zm-1 19.9A9 9 0 0 1 4.2 9.3L9 14v1a2 2 0 0 0 2 2zm6.9-2.5A2 2 0 0 0 16 17h-1v-3a1 1 0 0 0-1-1H8v-2h2a1 1 0 0 0 1-1V8h2a2 2 0 0 0 2-2v-.4a9 9 0 0 1 2.9 12.8z"/></svg>
        t.wrenfeld@ValmiraHealth.example
      </li>
    </ul>
  </section>

  <section class="card card--back">
    <div class="wave-field" role="img" aria-label="Abstract flowing wave pattern in layered blue tones"></div>
    <div class="brand">
      <div class="brand__name">VALMIRA</div>
      <div class="brand__tagline">Integrative Holistic Medicine</div>
    </div>
  </section>

</main>
</body>
</html>
```